Research and Innovation programme/projects in WOOD based industries

1.Pramenova s.r.o. (offical registered brand name of our company)
-Managing technology development projects
-International cooperation and development European projects
Our company was founded in 2008 and started to work as a counsilary company operating in the section of european funds administrated by Czech republic. Nowadays we are specializing on projects in the sphere of science and research co-financed by EU.Since 6.6.2013 we are registered under European comission for a purpose of broad support of transnational projects.

Target Market(s)

We are primarily focused on european companies, which stand behind the latest research and innovation of sawing, planing, glulam and logging technologies based on wooden materials.

Coding

Coded - Design and coding required

Number of Pages Required

5+ page

Font styles to use
Serif

Colors
cadf82
abd037
9bcb3c
fee18a
ffcf3e
ffc214

Requirements
Must have
• The web will exist in three possible languages in czech, english and deutsch.
• First page : introduction of a company
• Second page : Area of expertise
• Third page: servicies our company provides
• Fourth page: Our partners
• Fifth page: Conditions of our servicies
• Sixth page: Succesful projects
• - we would also love if we had possibility to add videos about our successful projects
• Seventh: Our team
• We are serious company in the sphere of funds and counsilary servicies, that is why we would love to have web design as representative as possible
• Take on mind that that we are specializing on development management, try to apply that on your design
• In the section of contacts, we would love to have photos of our team,
• This is our current site: http://www.pramenova-example.eu/cz/partneri.html
• This is how our concurency sites are lookin. Take these designs as an slight inspiration.
• http://www.lumatrava-example.sk/en/
• https://www2.brenvick-example.com/global/en.html
Nice to have
• Visible logo on the front page for the visitor.
• As a inspiration we provided link for our current web design, but we dont want to copy the current style, just look at the logo and the pages that exists on current web.
• !!!!!!We also uploaded file, where we explain how our cooperation with partner works. Especially in the part 2. section of service. Take that as an ispiration too, or use that to understand, what our company do.
Should not have
• We are serious company in the sphere of funds and counsilary servicies, that is why we would love to have web design representative as possible

```html
<!DOCTYPE html>
<html lang="en">
<head>
<meta charset="utf-8">
<title>Pramenova s.r.o. – Development Management</title>
<link rel="stylesheet" href="https://fonts.googleapis.com/css2?family=Fira+Sans:wght@400;500;600&family=Open+Sans:wght@400;600;700&display=swap">
<style>
:root{
  --green:#7cb82f;
  --green-dark:#1d7a32;
  --green-mid:#2f9a3e;
  --orange:#f7931e;
  --orange-light:#ffb21f;
  --ink:#111;
  --text:#555;
  --grey-bg:#f2f2f2;
  --footer:#1e1e1e;
  --white:#fff;
}
*{box-sizing:border-box;margin:0;padding:0}
html,body{width:1200px;height:5217px;overflow:hidden}
body{font-family:"Open Sans",sans-serif;color:var(--text);background:var(--white);position:relative}
h1,h2,h3{font-family:"Fira Sans",sans-serif;font-weight:500;color:var(--ink)}
.section-title{text-align:center;font-size:44px;line-height:1}
.rule{display:block;width:42px;height:4px;background:var(--orange);margin:22px auto 0}
.btn{display:inline-block;background:var(--orange);color:var(--white);font-family:"Fira Sans",sans-serif;font-size:17px;text-align:center}

/* header */
.topbar{height:96px;border-top:4px solid var(--orange);position:relative}
.brand{position:absolute;left:90px;top:30px;display:flex;align-items:center;gap:14px}
.brand-square{width:30px;height:30px;background:var(--green)}
.brand-name{font-family:"Fira Sans",sans-serif;font-weight:600;font-size:24px;color:var(--green-dark);line-height:1}
.address{position:absolute;left:530px;top:28px;display:flex;gap:22px;font-size:15px;line-height:26px;color:#444}
.pin-box{width:40px;height:40px;border:1px solid #f3c79a;display:flex;align-items:center;justify-content:center}
.lang{position:absolute;left:980px;top:32px;width:128px;height:38px;border:1px solid #ccc;display:flex;font-size:13px;color:#777}
.lang span{flex:1;display:flex;align-items:center;padding-left:10px;gap:8px}
.flag{width:22px;height:14px;background:#2b3f8c}
.lang i{width:36px;border-left:1px solid #ccc;display:flex;align-items:center;justify-content:center}
.nav{height:52px;background:var(--green);display:flex;align-items:center;padding-left:104px;gap:34px}
.nav a{color:var(--white);font-size:14.5px;font-weight:600;text-transform:uppercase;text-decoration:none}

/* hero */
.hero{height:555px;position:relative;text-align:center;background:linear-gradient(180deg,#3b3f42 0%,#5a5650 45%,#8a7660 75%,#6a5a48 100%)}
.hero h1{position:absolute;top:132px;left:0;right:0;color:var(--white);font-size:60px;font-weight:500;line-height:66px}
.hero .btn{position:absolute;left:495px;top:303px;width:210px;height:54px;line-height:54px;font-size:22px}
.scroll-down{position:absolute;left:576px;top:471px}

/* welcome */
.welcome{height:532px;padding-top:92px;text-align:center}
.welcome p{width:960px;margin:46px auto 0;font-size:16.5px;line-height:35px;color:#444}
.welcome .btn{margin-top:44px;width:166px;height:52px;line-height:52px}

/* expertise */
.expertise{height:631px;position:relative;overflow:visible}
.expertise .bg{position:absolute;inset:0}
.expertise h2{position:absolute;top:92px;left:0;right:0;text-align:center;color:var(--white);font-size:46px}
.exp-cards{position:absolute;top:181px;left:110px;display:flex;gap:27px}
.exp-card{width:310px;height:340px;background:var(--white);text-align:center;position:relative;padding-top:36px}
.exp-card h3{font-size:22px;color:#222;margin-top:22px}
.exp-card p{font-size:15.5px;line-height:32px;color:#777;margin-top:16px;padding:0 18px}
.corner{position:absolute;right:0;bottom:0;width:0;height:0;border-left:34px solid transparent;border-bottom:28px solid var(--orange)}
.corner b{position:absolute;right:4px;top:9px;color:#fff;font-size:14px;line-height:1;font-weight:400}

/* services */
.services{height:664px;padding-top:102px}
.svc-grid{display:grid;grid-template-columns:repeat(4,240px);gap:20px 20px;width:1020px;margin:60px auto 0}
.svc{height:195px;background:var(--white);box-shadow:0 2px 12px rgba(0,0,0,.12);display:flex;flex-direction:column;align-items:center;justify-content:center;text-align:center;font-size:15.5px;font-weight:700;color:#222;line-height:25px}
.svc svg{margin-bottom:14px}
.svc-brand .brand-square{margin:0 0 14px}
.svc-brand .brand-name{font-size:22px}

/* partners */
.partners{height:338px;padding-top:72px}
.partner-row{display:flex;justify-content:center;gap:120px;margin-top:60px;align-items:center}
.badge{background:#d9d9d9}

/* conditions */
.conditions{height:557px;position:relative;background:var(--grey-bg)}
.conditions .accent{position:absolute;right:0;top:0;width:335px;height:100%;background:var(--orange)}
.conditions h2{position:absolute;left:88px;top:86px;font-size:46px;line-height:48px;color:#111}
.conditions .rule-left{position:absolute;left:88px;top:205px;width:48px;height:4px;background:var(--orange)}
.cond-list{position:absolute;left:88px;top:240px;width:440px;list-style:none;font-size:15.5px;line-height:33px;color:#555}
.cond-list li{padding-left:28px;position:relative;text-align:justify}
.cond-list li::before{content:"»";position:absolute;left:0;color:var(--orange)}
.cond-photo{position:absolute;left:583px;top:51px;width:550px;height:457px;background:linear-gradient(180deg,#b6c7d8 0%,#c4b8a6 30%,#9d8a78 70%,#8f8f86 100%)}

/* projects */
.projects{height:675px;padding-top:102px}
.proj-row{display:flex;gap:22px;width:1020px;margin:60px auto 0}
.proj{width:238px;height:281px;position:relative}
.proj .label{position:absolute;left:16px;bottom:18px;color:#fff;font-family:"Fira Sans",sans-serif;font-size:17px;font-weight:500}
.proj .mark{position:absolute;left:16px;bottom:48px;width:28px;height:18px;background:var(--orange-light)}
.arrows{display:flex;justify-content:center;gap:26px;margin-top:42px}
.arrows span{width:48px;height:46px;display:flex;align-items:center;justify-content:center}

/* team */
.team{height:570px;position:relative;background:var(--grey-bg);padding-top:92px}
.team .tri{position:absolute;top:0;left:0}
.team h2,.team .rule{position:relative}
.member{position:absolute;top:220px;display:flex}
.member .photo{width:222px;height:248px;background:linear-gradient(180deg,#6d6a5f,#c9a98f 55%,#3d3a36)}
.member .info{padding:60px 0 0 72px}
.member .name{font-size:17px;color:#333}
.member .role{font-size:14.5px;color:#777;margin-top:2px}
.member hr{border:0;border-top:1px solid #ccc;width:200px;margin:18px 0 22px}
.member .line{display:flex;align-items:center;gap:14px;font-size:14px;color:#444;line-height:26px}

/* newsletter */
.newsletter{height:156px;background:var(--green);position:relative}
.newsletter h3{position:absolute;left:180px;top:62px;color:#fff;font-family:"Open Sans",sans-serif;font-weight:400;font-size:21px}
.newsletter .field{position:absolute;left:529px;top:60px;width:441px;height:46px;background:#fff;font-size:13px;color:#555;padding:15px 18px}
.newsletter .send{position:absolute;left:970px;top:60px;width:50px;height:46px;background:var(--orange);display:flex;align-items:center;justify-content:center}

/* footer */
.footer{height:391px;background:var(--footer);position:relative;color:#ccc;font-size:13px}
.fcol{position:absolute;top:60px}
.fcol h4{color:#fff;font-size:15px;font-weight:400;margin-bottom:22px}
.fcol a,.fcol p{display:block;color:#ccc;text-decoration:none;line-height:31px}
.social{display:flex;gap:18px;margin-top:4px}
.copy{position:absolute;left:0;right:0;bottom:14px;text-align:center;font-size:12.5px;color:#ccc}
</style>
</head>
<body>

<header class="topbar">
  <div class="brand">
    <div class="brand-square"></div>
    <div class="brand-name">Pramenova s.r.o.</div>
  </div>
  <div class="address">
    <div class="pin-box">
      <svg width="16" height="20" viewBox="0 0 16 20"><path d="M8 1a6 6 0 0 0-6 6c0 4.5 6 12 6 12s6-7.5 6-12a6 6 0 0 0-6-6z" fill="none" stroke="#f7931e" stroke-width="1.8"/><circle cx="8" cy="7" r="2.2" fill="#f7931e"/></svg>
    </div>
    <div>Pramenova s.r.o, ID 4410, Lindenweg 14<br>02700 Brennfeld</div>
  </div>
  <div class="lang"><span><b class="flag"></b>Eng</span><i><svg width="8" height="5"><path d="M0 0h8L4 5z" fill="#777"/></svg></i></div>
</header>

<nav class="nav">
  <a>The Enterprise</a><a>Leistungsen</a><a>Our Projects</a><a>Cooperation Partners</a><a>Calls for Cooperation</a><a>Contact</a>
</nav>

<section class="hero" role="img" aria-label="Wood processing hall with stacked timber panels">
  <h1>We Are Specializing On<br>Development Management</h1>
  <a class="btn">Get started &#10140;</a>
  <svg class="scroll-down" width="48" height="48" viewBox="0 0 48 48"><circle cx="24" cy="24" r="22" fill="none" stroke="#fff" stroke-width="2"/><path d="M17 21l7 7 7-7" fill="none" stroke="#fff" stroke-width="2"/></svg>
</section>

<section class="welcome">
  <h2 class="section-title">Welcome to Pramenova Sro</h2>
  <span class="rule"></span>
  <p>Our company was founded in 2008 and started to work as a counsilary company operating in the section of European funds administrated by Czech republic. Nowadays we are specialising on projects in the sphere of science and research co-financed by EU.Since 6.6.2013 we are registered under European commission for a purpose of broad support of transnational projects.</p>
  <a class="btn">Learn More</a>
</section>

<section class="expertise">
  <svg class="bg" width="1200" height="650" viewBox="0 0 1200 650" role="img" aria-label="Timber yard in orange and green tones">
    <defs>
      <linearGradient id="expG" x1="0" y1="0" x2="1" y2="1"><stop offset="0" stop-color="#2a8a3a"/><stop offset="1" stop-color="#1f7a32"/></linearGradient>
      <linearGradient id="expO" x1="0" y1="0" x2="1" y2="0"><stop offset="0" stop-color="#f7931e"/><stop offset="1" stop-color="#f9a53a"/></linearGradient>
    </defs>
    <rect width="1200" height="631" fill="url(#expG)"/>
    <polygon points="0,0 1200,0 1200,70 600,631 0,110" fill="url(#expO)" opacity=".95"/>
    <polygon points="0,0 520,0 0,280" fill="#e98a17"/>
    <polygon points="1200,631 1200,250 800,631" fill="#1a6d2c"/>
    <polygon points="580,631 620,631 600,650" fill="#f7931e"/>
  </svg>
  <h2>Area of Expertise</h2>
  <div class="exp-cards">
    <div class="exp-card">
      <svg width="90" height="90" viewBox="0 0 90 90" fill="none" stroke="#f7931e" stroke-width="2.5"><circle cx="32" cy="32" r="14"/><circle cx="32" cy="32" r="6"/><circle cx="58" cy="50" r="13"/><path d="M53 66h10M54 72h8M58 37v-6"/><path d="M78 20a36 36 0 0 0-18-12M12 60a36 36 0 0 0 14 18"/></svg>
      <h3>INNOVATION PROGRAMME</h3>
      <p>Sed ut perspiciatis unde omnis iste natus error sit voluptatem tium loremque laudantium, illo</p>
      <span class="corner"><b>+</b></span>
    </div>
    <div class="exp-card">
      <svg width="90" height="90" viewBox="0 0 90 90" fill="none" stroke="#f7931e" stroke-width="2.5"><path d="M38 60c0-10-10-14-10-26a17 17 0 0 1 34 0c0 12-10 16-10 26z"/><path d="M38 66h14M40 72h10M45 4v8M18 14l6 6M72 14l-6 6"/><circle cx="64" cy="56" r="9"/><path d="M70 62l12 12"/></svg>
      <h3>RESEARCH</h3>
      <p>Sed ut perspiciatis unde omnis iste natus error sit voluptatem tium loremque laudantium, illo</p>
      <span class="corner"><b>+</b></span>
    </div>
    <div class="exp-card">
      <svg width="90" height="90" viewBox="0 0 90 90" fill="none" stroke="#f7931e" stroke-width="2.5"><path d="M30 60l30-30c6-6 14-8 20-8 0 6-2 14-8 20L42 72z"/><circle cx="60" cy="38" r="5"/><path d="M30 60l-10-2 12-12M42 72l2 10 12-12M26 66l-10 10M18 8v22M18 8h14l-4 5 4 5H18"/></svg>
      <h3>SUCCESFUL PROJECTS</h3>
      <p>Sed ut perspiciatis unde omnis iste natus error sit voluptatem tium loremque laudantium, illo</p>
      <span class="corner"><b>+</b></span>
    </div>
  </div>
</section>

<section class="services">
  <h2 class="section-title">Services Our Company Provides</h2>
  <div class="svc-grid">
    <div class="svc"><svg width="50" height="50" viewBox="0 0 50 50" fill="none" stroke="#2f9a3e" stroke-width="2"><circle cx="25" cy="16" r="10"/><path d="M20 16l4 4 7-7M4 28l10 14h12M46 28L36 42H26"/></svg>Projectcoordination</div>
    <div class="svc"><svg width="50" height="50" viewBox="0 0 50 50" fill="none" stroke="#2f9a3e" stroke-width="2"><rect x="10" y="6" width="26" height="36"/><path d="M16 14h14M16 20h14M16 26h8"/><circle cx="36" cy="36" r="8"/></svg>Project financing</div>
    <div class="svc"><svg width="50" height="50" viewBox="0 0 50 50" fill="none" stroke="#2f9a3e" stroke-width="2"><circle cx="30" cy="30" r="14"/><path d="M16 30h28M30 16c-6 8-6 20 0 28M30 16c6 8 6 20 0 28"/><circle cx="12" cy="10" r="5"/></svg>Technology and foreign<br>trade projects</div>
    <div class="svc"><svg width="50" height="50" viewBox="0 0 50 50" fill="none" stroke="#2f9a3e" stroke-width="2"><path d="M20 26c0-5-5-7-5-13a10 10 0 0 1 20 0c0 6-5 8-5 13z"/><path d="M21 31h8M4 30l10 14h22l10-14"/></svg>Export promotion</div>
    <div class="svc svc-brand"><div class="brand-square"></div><div class="brand-name">Pramenova s.r.o.</div></div>
    <div class="svc"><svg width="50" height="50" viewBox="0 0 50 50" fill="none" stroke="#2f9a3e" stroke-width="2"><circle cx="25" cy="25" r="12"/><circle cx="25" cy="25" r="5"/><path d="M25 4v6M25 40v6M4 25h6M40 25h6M10 10l4 4M36 36l4 4M40 10l-4 4M10 40l4-4"/></svg>Projects in the<br>framework of international<br>cooperation</div>
    <div class="svc"><svg width="50" height="50" viewBox="0 0 50 50" fill="none" stroke="#2f9a3e" stroke-width="2"><rect x="6" y="6" width="30" height="30"/><circle cx="21" cy="18" r="5"/><path d="M12 32c2-6 16-6 18 0"/><rect x="30" y="26" width="14" height="18"/></svg>EU projects</div>
    <div class="svc"><svg width="50" height="50" viewBox="0 0 50 50" fill="none" stroke="#2f9a3e" stroke-width="2"><circle cx="20" cy="14" r="8"/><path d="M26 20l8 8M8 44V34M16 44V28M24 44V32M32 44V24M40 44V18M36 10l8-4"/></svg>International<br>Development Projects</div>
  </div>
</section>

<section class="partners">
  <h2 class="section-title">Our Partners</h2>
  <span class="rule"></span>
  <div class="partner-row">
    <div class="badge" style="width:124px;height:46px"></div>
    <div class="badge" style="width:134px;height:76px"></div>
    <div class="badge" style="width:206px;height:40px"></div>
  </div>
</section>

<section class="conditions">
  <div class="accent"></div>
  <h2>Conditions of Our<br>Services</h2>
  <span class="rule-left"></span>
  <ul class="cond-list">
    <li>Sed ut perspiciatis unde omnis iste natus error sit</li>
    <li>Tatem accusantium doloremque laudantium, totam</li>
    <li>Rem aperiam, eaque ipsa quae ab illo inventore verita</li>
    <li>Et quasi architecto beatae vitae dicta sunt explicabo.</li>
    <li>Nemo enim ipsam voluptatem quia voluptas sit natur</li>
    <li>Aut odit aut fugit, sed quia consequuntur magni Ores</li>
    <li>Eos qui ratione voluptatem sequi nesciunt.</li>
  </ul>
  <div class="cond-photo" role="img" aria-label="Newly built office building under construction with scaffolding"></div>
</section>

<section class="projects">
  <h2 class="section-title">Successful Projects</h2>
  <span class="rule"></span>
  <div class="proj-row">
    <div class="proj" role="img" aria-label="Forestry tractor in front of a workshop" style="background:linear-gradient(180deg,#cfd3d6,#6a6a60 60%,#2f3a2c)"><span class="mark"></span><span class="label">SAWMILL TECHNOLOGY</span></div>
    <div class="proj" role="img" aria-label="Wood processing machinery in a workshop" style="background:linear-gradient(180deg,#a88f72,#7a7166 55%,#3d3a36)"><span class="mark"></span><span class="label">LOREM IPSUM</span></div>
    <div class="proj" role="img" aria-label="Modern industrial hall exterior" style="background:linear-gradient(180deg,#8fb0d8,#c8c8c4 45%,#7a7a76)"><span class="mark"></span><span class="label">LOREM IPSUM</span></div>
    <div class="proj" role="img" aria-label="Timber production line inside a factory" style="background:linear-gradient(180deg,#8a8c88,#6b6a60 55%,#3a3632)"><span class="mark"></span><span class="label">LOREM IPSUM</span></div>
  </div>
  <div class="arrows">
    <span style="background:var(--green-dark)"><svg width="12" height="16"><path d="M10 2L3 8l7 6" fill="none" stroke="#fff" stroke-width="2"/></svg></span>
    <span style="background:var(--green)"><svg width="12" height="16"><path d="M2 2l7 6-7 6" fill="none" stroke="#fff" stroke-width="2"/></svg></span>
  </div>
</section>

<section class="team">
  <svg class="tri" width="1200" height="190" viewBox="0 0 1200 190"><polygon points="0,0 1200,0 600,190" fill="#e9e9e9"/></svg>
  <h2 class="section-title">Our Team</h2>
  <span class="rule"></span>
  <div class="member" style="left:90px">
    <div class="photo" role="img" aria-label="Portrait photo of Tomas Hradek"></div>
    <div class="info">
      <div class="name">Tomas Hradek</div>
      <div class="role">Geschäftsführer</div>
      <hr>
      <div class="line"><svg width="14" height="14" viewBox="0 0 14 14"><path d="M3 1l2 3-1.5 1.5a8 8 0 0 0 5 5L10 9l3 2-1.5 2.5C6 13 1 8 .5 2.5z" fill="#2f9a3e"/></svg>+420 700 555 120</div>
      <div class="line"><svg width="14" height="11" viewBox="0 0 14 11"><rect width="14" height="11" fill="#2f9a3e"/><path d="M0 0l7 6 7-6" fill="none" stroke="#fff" stroke-width="1.2"/></svg>hradek@pramenova-example.eu</div>
    </div>
  </div>
  <div class="member" style="left:643px">
    <div class="photo" role="img" aria-label="Portrait photo of Lenka Dvorska" style="background:linear-gradient(180deg,#efeae4,#c88e72 55%,#7a3a28)"></div>
    <div class="info">
      <div class="name">Mgr. Lenka Dvorska</div>
      <div class="role">Project manager</div>
      <hr>
      <div class="line"><svg width="14" height="14" viewBox="0 0 14 14"><path d="M3 1l2 3-1.5 1.5a8 8 0 0 0 5 5L10 9l3 2-1.5 2.5C6 13 1 8 .5 2.5z" fill="#2f9a3e"/></svg>+420 700 555 120</div>
      <div class="line"><svg width="14" height="11" viewBox="0 0 14 11"><rect width="14" height="11" fill="#2f9a3e"/><path d="M0 0l7 6 7-6" fill="none" stroke="#fff" stroke-width="1.2"/></svg>dvorska@pramenova-example.eu</div>
    </div>
  </div>
</section>

<section class="newsletter">
  <svg style="position:absolute;left:590px;top:0" width="20" height="10"><path d="M0 0h20L10 10z" fill="#f2f2f2"/></svg>
  <h3>SIGN UP OUR NEWSLETTER</h3>
  <div class="field">Email Address</div>
  <div class="send"><svg width="18" height="18" viewBox="0 0 18 18"><path d="M1 8l16-7-5 16-3-6z" fill="none" stroke="#fff" stroke-width="1.6"/></svg></div>
</section>

<footer class="footer">
  <div class="fcol" style="left:117px"><h4>COMPANY</h4><a>The Enterprise</a><a>Leistungsen</a><a>Our Projects</a><a>Cooperation Partners</a><a>Calls For Cooperation</a><a>Contact</a></div>
  <div class="fcol" style="left:373px"><h4>CONTACT</h4><p style="line-height:28px">Corporate Office<br>(800) 555-0142<br>info@pramenova-example.eu</p></div>
  <div class="fcol" style="left:641px"><h4>ADDRESS</h4><p style="line-height:30px">Pramenova s.r.o, ID 4410<br>Lindenweg 14<br>02700 Brennfeld</p></div>
  <div class="fcol" style="left:972px"><h4>MY ACCOUNT</h4><a>Log in</a><a>Sign Up</a><h4 style="margin-top:24px;margin-bottom:14px">FOLLOW US</h4>
    <div class="social"><svg width="12" height="12"><circle cx="6" cy="6" r="5" fill="#fff"/></svg><svg width="12" height="12"><circle cx="6" cy="6" r="5" fill="#fff"/></svg><svg width="12" height="12"><circle cx="6" cy="6" r="5" fill="#fff"/></svg><svg width="12" height="12"><circle cx="6" cy="6" r="5" fill="#fff"/></svg></div>
  </div>
  <div class="copy">© 2019 The Company Name. All rights Reserved.Privacy Policy | Terms Of Use</div>
</footer>

</body>
</html>
```